Fern Lattice Table & Chair Rentals

We need a business card for a table and chair rental company. We rent tables and chairs for weddings, funerals, business events and parties. We want something that looks clean and elegant while not being too busy. We would like colors in the green and blue hues and avoiding anything orange. We want to make sure the font is large enough to be seen easily.

Target Market(s)

Wedding & Event Rentals

Industry/Entity Type

Events

Contact Information for Business Card

Fern Lattice, sales@fernlatticerentals.com, fernlatticerentals.com, 360-555-0182

Requirements
Must have
• Easy to read font
Should not have
• Orange anywhere in the design

```html
<!DOCTYPE html>
<html lang="en">
<head>
<meta charset="utf-8">
<title>Fern Lattice Table &amp; Chair Rentals – Business Card</title>
<link rel="stylesheet" href="https://fonts.googleapis.com/css2?family=Roboto:wght@400;500&family=Roboto+Condensed:wght@400&display=swap">
<style>
  :root {
    --page-bg: #e6e8e6;
    --card-black: #0b0b0b;
    --card-white: #ffffff;
    --band-green: #3fae8c;
    --band-blue: #3b94c8;
    --ink-dark: #0e1a1f;
    --ink-light: #f4f4f4;
    --divider: #123038;
  }
  * { margin: 0; padding: 0; box-sizing: border-box; }
  html, body {
    width: 1200px; height: 892px; overflow: hidden;
    background: var(--page-bg);
    font-family: "Roboto", Arial, sans-serif;
  }
  .canvas { position: relative; width: 1200px; height: 892px; }

  .card {
    position: absolute;
    width: 640px; height: 366px;
    background: var(--card-black);
    overflow: hidden;
    box-shadow: 0 8px 22px rgba(0,0,0,0.25);
  }
  .card--back  { left: 480px; top: 60px; }
  .card--front { left: 80px;  top: 466px; }

  .brand-name {
    position: absolute;
    color: var(--ink-light);
    font-family: "Roboto", Arial, sans-serif;
    font-weight: 500;
    font-size: 62px;
    line-height: 1;
    white-space: nowrap;
  }
  .brand-tagline {
    position: absolute;
    color: var(--ink-light);
    font-weight: 400;
    font-size: 33px;
    line-height: 1;
    white-space: nowrap;
  }

  .band {
    position: absolute; left: 0; width: 100%;
    background: linear-gradient(90deg, var(--band-green) 0%, var(--band-blue) 100%);
    border-top: 7px solid var(--card-white);
    border-bottom: 7px solid var(--card-white);
  }

  /* back */
  .card--back .brand-name { left: 150px; top: 70px; }
  .card--back .brand-tagline { left: 150px; top: 150px; }
  .card--back .band { top: 232px; height: 74px; }
  .hours {
    display: flex; justify-content: space-between; align-items: center;
    height: 100%; padding: 0 28px;
    font-family: "Roboto Condensed", Arial, sans-serif;
    font-size: 20px; color: var(--ink-dark);
  }

  /* front */
  .card--front .brand-name { left: 190px; top: 26px; }
  .card--front .brand-tagline { left: 190px; top: 104px; }
  .card--front .band { top: 170px; height: 136px; }
  .contact {
    position: relative; height: 100%;
    display: flex; align-items: center;
  }
  .contact__phone {
    width: 300px; padding-left: 34px;
    font-size: 38px; color: var(--ink-dark);
  }
  .contact__divider { position: absolute; left: 300px; top: 16px; }
  .contact__online {
    padding-left: 36px;
    font-size: 22px; line-height: 1.35; color: var(--ink-dark);
  }
</style>
</head>
<body>
<main class="canvas">

  <section class="card card--back" aria-label="Business card back">
    <p class="brand-name">Fern Lattice</p>
    <p class="brand-tagline">Table and Chair Rentals</p>
    <div class="band">
      <div class="hours">
        <span>Mon-Fri: 8am to 6pm</span>
        <span>Saturday: 8am to 4pm</span>
        <span>Sunday: 9am to 1pm</span>
      </div>
    </div>
  </section>

  <section class="card card--front" aria-label="Business card front">
    <p class="brand-name">Fern Lattice</p>
    <p class="brand-tagline">Table and Chair Rentals</p>
    <div class="band">
      <div class="contact">
        <p class="contact__phone">360-555-0182</p>
        <svg class="contact__divider" width="12" height="90" viewBox="0 0 12 90" aria-hidden="true">
          <line x1="10" y1="2" x2="2" y2="88" stroke="var(--divider)" stroke-width="2"/>
        </svg>
        <div class="contact__online">
          <p>www.fernlatticerentals.com</p>
          <p>sales@fernlatticerentals.com</p>
        </div>
      </div>
    </div>
  </section>

</main>
</body>
</html>
```